New Business Card for our Indoor Golf Training Facility

We are looking for designs for a new business card for our indoor golf training facility. Attached is our logo, our logo with our slogan, and here is our elevator pitch (What makes us different from the others) not sure if all the info will fit on one card, maybe you can condense the elevator pitch? here is the info

Elevator Pitch
We work with serious golfers and those that want to be serious golfers…
to make you better, faster, at all phases of the game…
We use the same state-of-the-art technology as professional golfers…
which produces data sets that shows your improvement in real time.
Our facility is available 24/7 to our members, which allows you to improve on your time.

our website: www.birchpinlinks.com

Target Market(s)

Golfers

Font styles to use
Serif
Sans Serif

Colors
ec1f27
f59195
fbd4d5
919191
d3d3d3
1b1b1b

Requirements
Must have
• our logo or our logo with the slogan, elevator pitch (can be condensed or shortened)

```html
<!DOCTYPE html>
<html lang="en">
<head>
<meta charset="utf-8">
<title>Birch Pin Links – Business Card</title>
<link href="https://fonts.googleapis.com/css2?family=Roboto:wght@300;400;700&family=Roboto+Condensed:wght@400;700&display=swap" rel="stylesheet">
<style>
  :root {
    --red: #ec1f27;
    --red-soft: #f0504f;
    --white: #ffffff;
    --grey: #808080;
    --ink: #1b1b1b;
    --page: #efefef;
  }
  * { box-sizing: border-box; margin: 0; padding: 0; }
  html, body { width: 1200px; height: 950px; overflow: hidden; }
  body {
    background: var(--page);
    font-family: "Roboto", Arial, sans-serif;
    position: relative;
  }
  .card {
    position: absolute;
    left: 250px;
    width: 700px;
    height: 400px;
    border-radius: 26px;
    overflow: hidden;
    box-shadow: 0 6px 18px rgba(0,0,0,0.18);
  }
  .card--front { top: 55px; background: var(--white); display: flex; }
  .card--back { top: 500px; background: var(--grey); color: var(--white); text-align: center; }

  .contact-panel {
    width: 330px;
    background: linear-gradient(135deg, var(--red) 0%, var(--red-soft) 100%);
    color: var(--white);
    padding: 70px 0 0 48px;
  }
  .person-name { font-weight: 700; font-size: 26px; letter-spacing: 0.5px; text-transform: uppercase; }
  .person-role { font-size: 18px; font-weight: 400; margin-bottom: 34px; text-transform: uppercase; }
  .address { font-size: 17px; line-height: 1.4; margin-bottom: 16px; }
  .contact-list { list-style: none; font-size: 17px; line-height: 1.55; }
  .contact-list li { display: flex; align-items: center; gap: 10px; }
  .contact-list svg { width: 14px; height: 14px; flex: none; }

  .brand-panel {
    flex: 1;
    display: flex;
    align-items: center;
    padding-left: 22px;
  }
  .brand-mark { width: 60px; height: 60px; border: 5px solid var(--red); border-radius: 50%; flex: none; margin-right: 14px; }
  .brand-text { white-space: nowrap; }
  .brand-name { color: var(--red); font-weight: 700; font-size: 34px; line-height: 1; }
  .brand-slogan { color: var(--red); font-weight: 300; font-size: 15px; margin-top: 6px; }

  .back-mark {
    width: 118px; height: 118px; border: 8px solid var(--white); border-radius: 50%;
    margin: 46px auto 22px;
  }
  .pitch-title { font-family: "Roboto Condensed", Arial, sans-serif; font-weight: 700; font-size: 26px; letter-spacing: 1px; margin-bottom: 14px; }
  .pitch-text { font-family: "Roboto Condensed", Arial, sans-serif; font-size: 16px; line-height: 1.5; padding: 0 40px; }
</style>
</head>
<body>
  <section class="card card--front">
    <div class="contact-panel">
      <p class="person-name">Dana Whitfield</p>
      <p class="person-role">CEO/Founder</p>
      <p class="address">418 W. Alder Rd.<br>Unit B3<br>Fairbrook, OH 45990</p>
      <ul class="contact-list">
        <li><svg viewBox="0 0 16 16"><path fill="#fff" d="M3 1l3 3-1.5 2c1 2 3 4 5 5L11.5 9.5l3 3L12.5 15C6 14 2 10 1 3.5z"/></svg>555-014-2290</li>
        <li><svg viewBox="0 0 16 16"><rect x="1" y="3" width="14" height="10" fill="#fff"/><path d="M1 3l7 6 7-6" stroke="#ec1f27" stroke-width="1.5" fill="none"/></svg>info@birchpinlinks.com</li>
        <li><svg viewBox="0 0 16 16"><circle cx="8" cy="8" r="7" fill="#fff"/></svg>www.birchpinlinks.com</li>
      </ul>
    </div>
    <div class="brand-panel">
      <div class="brand-mark"></div>
      <div class="brand-text">
        <p class="brand-name">Birch Pin Links</p>
        <p class="brand-slogan">Every Swing Counts. Keep Climbing.</p>
      </div>
    </div>
  </section>

  <section class="card card--back">
    <div class="back-mark"></div>
    <h2 class="pitch-title">ELEVATOR PITCH :</h2>
    <p class="pitch-text">
      Coaching for dedicated players and anyone ready to take the game seriously…<br>
      helping you improve quickly across driving, irons, short game and putting…<br>
      Our bays run the same tour-grade launch monitors the pros trust…<br>
      so every session gives clear numbers that track your progress live.<br>
      Members can train any hour, day or night, on a schedule that suits them.
    </p>
  </section>
</body>
</html>
```